Social Media Graphics - Oakline Push REVISED

Create 6-7 individual social media graphics (square size) to encourage folks to join our online course called:

The Harvest Ledger Circle
How to Launch a Multi-Million Business From Scratch
Sign Up Today!

IMPORTANT: Make the largest and most prominent text on the graphic be: How to Launch a Multi-Million Business From Scratch

For the color scheme of the graphics, let's try a blue color palette; make sure the graphics appeal to both men and women

Make sure each graphic contains 1 of the 3 pics attached (crop pic as needed); and make sure one of the graphics is all TEXT only.

Target Market(s)

men and women looking to start a business

Industry/Entity Type

Entrepreneurship

Colors
0054AA
0677BA
7BADD7
CADEEF
E8F1F8

Requirements
Must have
• All the text and use the 3 pics provided; one graphic can be all text; Simple, modern design that's easy to read

```html
<!DOCTYPE html>
<html lang="en">
<head>
<meta charset="utf-8">
<title>The Harvest Ledger Circle – Sign Up Today</title>
<link rel="stylesheet" href="https://fonts.googleapis.com/css2?family=Barlow+Condensed:wght@700;800&display=swap">
<style>
  :root {
    --blue-deep: #0f4ea3;
    --blue-mid: #1a63b8;
    --blue-bright: #0677ba;
    --cyan: #0aaee6;
    --navy-band: #1f3479;
    --outline: #123f8a;
    --white: #ffffff;
    --photo-a: #8d8f96;
    --photo-b: #3c4f86;
  }
  html, body {
    margin: 0;
    padding: 0;
    width: 1200px;
    height: 1200px;
    overflow: hidden;
    background: var(--blue-deep);
  }
  .poster {
    position: relative;
    width: 1200px;
    height: 1200px;
    overflow: hidden;
    font-family: "Barlow Condensed", "Arial Narrow", sans-serif;
    color: var(--white);
  }
  .backdrop {
    position: absolute;
    inset: 0;
  }
  .speakers-photo {
    position: absolute;
    left: 605px;
    top: 80px;
    width: 595px;
    height: 834px;
  }
  .course-name {
    position: absolute;
    left: 114px;
    top: 92px;
    margin: 0;
    font-weight: 800;
    font-size: 60px;
    line-height: 82px;
    letter-spacing: 4px;
    text-transform: uppercase;
  }
  .headline {
    position: absolute;
    left: 106px;
    top: 247px;
    margin: 0;
    font-weight: 800;
    font-size: 188px;
    line-height: 164px;
    letter-spacing: 2px;
    text-transform: uppercase;
    transform: scaleX(0.86);
    transform-origin: left top;
    -webkit-text-stroke: 3px var(--outline);
    paint-order: stroke fill;
    white-space: nowrap;
  }
  .headline span { display: block; }
  .headline-band {
    position: absolute;
    left: 0;
    top: 914px;
    width: 1200px;
    height: 148px;
    background: var(--navy-band);
    display: flex;
    align-items: center;
    justify-content: center;
  }
  .headline-band p {
    margin: 0;
    font-weight: 800;
    font-size: 107px;
    line-height: 1;
    letter-spacing: 2px;
    text-transform: uppercase;
    white-space: nowrap;
    transform: scaleX(0.95);
  }
  .cta-rule {
    position: absolute;
    top: 1150px;
    height: 2px;
    background: var(--white);
  }
  .cta-rule.left { left: 53px; width: 273px; }
  .cta-rule.right { left: 857px; width: 273px; }
  .cta {
    position: absolute;
    left: 326px;
    width: 531px;
    top: 1095px;
    height: 100px;
    display: flex;
    justify-content: center;
  }
  .cta p {
    margin: 0;
    font-weight: 800;
    font-size: 100px;
    line-height: 100px;
    letter-spacing: 6px;
    text-transform: uppercase;
    white-space: nowrap;
    transform: scaleX(0.72);
    flex-shrink: 0;
  }
</style>
</head>
<body>
<main class="poster">
  <svg class="backdrop" width="1200" height="1200" viewBox="0 0 1200 1200" aria-hidden="true">
    <defs>
      <linearGradient id="bgBase" x1="0" y1="0" x2="1" y2="1">
        <stop offset="0" stop-color="#1553a8"/>
        <stop offset="0.55" stop-color="#1a5fb5"/>
        <stop offset="1" stop-color="#1f78c8"/>
      </linearGradient>
      <linearGradient id="cyanWave" x1="0" y1="0" x2="1" y2="0">
        <stop offset="0" stop-color="#0db4ec"/>
        <stop offset="0.7" stop-color="#0a9fe0"/>
        <stop offset="1" stop-color="#1a7fd0"/>
      </linearGradient>
    </defs>
    <rect width="1200" height="1200" fill="url(#bgBase)"/>
    <path d="M0 330 C 300 240, 700 280, 1200 180 L 1200 0 L 0 0 Z" fill="#1652a6" opacity="0.6"/>
    <path d="M700 0 C 900 60, 1050 130, 1200 120 L 1200 0 Z" fill="#2a86d0" opacity="0.55"/>
    <path d="M0 600 C 250 510, 550 480, 1200 560 L 1200 700 C 700 620, 350 650, 0 760 Z" fill="url(#cyanWave)"/>
    <path d="M0 760 C 350 650, 700 620, 1200 700 L 1200 780 C 700 700, 350 740, 0 860 Z" fill="#1583d2" opacity="0.85"/>
    <path d="M0 470 C 300 380, 650 380, 1200 430" fill="none" stroke="#2b7ed0" stroke-width="28" opacity="0.5"/>
    <path d="M0 1000 C 400 880, 800 900, 1200 1000 L 1200 1200 L 0 1200 Z" fill="#1d6cc0" opacity="0.7"/>
    <path d="M0 1080 C 400 980, 800 1000, 1200 1090" fill="none" stroke="#2c86d6" stroke-width="30" opacity="0.5"/>
  </svg>

  <svg class="speakers-photo" viewBox="0 0 595 834" role="img" aria-label="Photo of the two course hosts, a man holding a microphone and a smiling woman in a blue blazer, standing on stage">
    <defs>
      <linearGradient id="photoTone" x1="0" y1="0" x2="1" y2="1">
        <stop offset="0" stop-color="var(--photo-a)"/>
        <stop offset="1" stop-color="var(--photo-b)"/>
      </linearGradient>
    </defs>
    <rect x="0" y="0" width="595" height="834" fill="url(#photoTone)" opacity="0.55"/>
  </svg>

  <h2 class="course-name">The Harvest<br>Ledger Circle</h2>

  <h1 class="headline">
    <span>How to</span>
    <span>Launch</span>
    <span>A Multi</span>
    <span>Million</span>
  </h1>

  <div class="headline-band">
    <p>Business From Scratch</p>
  </div>

  <span class="cta-rule left"></span>
  <div class="cta"><p>Sign Up Today</p></div>
  <span class="cta-rule right"></span>
</main>
</body>
</html>
```